TuneRoost - Music Industry App needs a top quality wordpress homepage

We need a modern responsive wordpress homepage built. Our website will only feature one page with the goal to get people to sign up to our app. A word document has been uploaded outlining the page content/sections.

Once the homepage is finalised, I will also need 2 landing pages built as part of this competition. It will be very similar to the homepage with the same layout etc but just feature different images and content. The homepage is for anyone (artists and venues) to find out about us but the landing pages will be artist or venue specific.

The completed work must be delivered as an exportable file into wordpress and be designed properly so no more work is needed to begin utilising as the actual website. The images used must be setup correctly for speed and quality also.

Target Market(s)

Venues and Artists.

Coding

Coded - Design and coding required

Requirements
Must have
• UPDATE: High Res Logo files attached
• Must be a modern looking website and be responsive. Must look good across all devices from desktop, to mobile and tablet. Needs to be very high quality.
• Please see the attached logo - I am waiting for the final high quality version and will reupload when complete but this will be enough to get you started for now. The website must have a dark base colour and have red/white elements to match the logo. The red colour used MUST match the red colour used in the logo.
• Please have a go at creating it how you think is best and provide feedback from there. I am leaving it very open to the designers so I can get the best website possible and lots of different ideas etc.

```html
<!DOCTYPE html>
<html lang="en">
<head>
<meta charset="utf-8">
<title>TuneRoost – Book Live Music</title>
<link href="https://fonts.googleapis.com/css2?family=Jost:wght@400;500;600;700&display=swap" rel="stylesheet">
<style>
:root{
  --red:#d7000f;
  --red-deep:#a8000b;
  --black:#0b0b0b;
  --dark:#151515;
  --white:#ffffff;
  --grey-bg:#e9e9e9;
  --text:#333333;
  --muted:#8a8a8a;
  --line:#bdbdbd;
}
*{margin:0;padding:0;box-sizing:border-box}
html,body{width:1200px;height:3718px;overflow:hidden}
body{font-family:'Jost',Arial,sans-serif;color:var(--text);background:var(--white);position:relative}
.abs{position:absolute}

/* Header */
.site-header{position:absolute;left:0;top:0;width:1200px;height:116px;background:var(--black);color:var(--white)}
.logo{position:absolute;left:172px;top:40px;display:flex;align-items:center;gap:10px;font-size:30px;font-weight:500;color:var(--white)}
.logo-dot{width:20px;height:20px;border-radius:50%;background:var(--red)}
.top-contact{position:absolute;right:174px;top:24px;display:flex;gap:26px;font-size:13px}
.top-contact span{display:flex;align-items:center;gap:10px}
.round-ico{width:26px;height:26px;border-radius:50%;background:var(--red);display:inline-flex;align-items:center;justify-content:center}
.main-nav{position:absolute;right:174px;top:72px;display:flex;gap:28px;font-size:13.5px}

/* Hero */
.hero{position:absolute;left:0;top:116px;width:1200px;height:632px;overflow:hidden}
.hero-photo{position:absolute;inset:0;background:
  radial-gradient(ellipse at 18% 30%,rgba(40,120,90,.55),transparent 55%),
  radial-gradient(ellipse at 80% 25%,rgba(190,30,60,.6),transparent 55%),
  radial-gradient(ellipse at 55% 60%,rgba(120,40,100,.5),transparent 60%),
  linear-gradient(180deg,#1d2a2a,#2a1a24 60%,#140f14)}
.hero h1{position:absolute;top:178px;width:100%;text-align:center;color:var(--white);font-size:60px;font-weight:600}
.hero .sub{position:absolute;top:256px;width:100%;text-align:center;color:var(--white);font-size:19px;font-weight:500}
.hero-form{position:absolute;left:274px;top:305px;width:650px;height:52px;display:flex;border-radius:26px;overflow:hidden}
.hero-form .field{flex:1;background:var(--white);font-size:12px;color:#555;padding:0 18px;display:flex;align-items:center}
.hero-form .btn{width:198px;background:var(--red);color:var(--white);font-weight:600;font-size:15px;display:flex;align-items:center;justify-content:center}
.hero-edge{position:absolute;left:0;bottom:0}

/* How it works */
.section-title{position:absolute;width:100%;text-align:center;font-size:40px;font-weight:400;color:#111}
.section-title b{color:var(--red);font-weight:600}
.steps-svg{position:absolute;left:0;top:960px}
.step-num{position:absolute;width:120px;text-align:center;font-size:36px;font-weight:600;color:#9a9a9a}
.step-text{position:absolute;width:140px;text-align:center;font-size:13.5px;line-height:22px;color:#333}

/* Why */
.why{position:absolute;left:0;top:1430px;width:1200px;height:606px;clip-path:polygon(0 0,50% 44px,100% 0,100% 100%,0 100%)}
.why-photo{position:absolute;inset:0;background:radial-gradient(ellipse at 50% 90%,#2c2c2c,transparent 60%),linear-gradient(180deg,#1a1a1a,#111 70%,#1b1b1b)}
.why .section-title{top:138px;color:var(--white)}
.feature-card{position:absolute;top:219px;width:202px;height:275px;border:1px solid #8f8f8f;text-align:center;color:var(--white)}
.feature-card svg{margin-top:24px}
.feature-card h3{font-size:16px;font-weight:600;margin-top:18px}
.feature-card p{font-size:12px;line-height:22px;margin:14px auto 0;width:170px;color:#ddd}

/* Audiences */
.audience{position:absolute;top:2036px;width:600px;height:657px}
.audience.venues{left:0;clip-path:polygon(0 0,100% 0,100% 604px,0 100%)}
.audience.artists{left:600px;background:var(--grey-bg);clip-path:polygon(0 0,100% 0,100% 100%,0 604px)}
.venue-photo{position:absolute;inset:0;background:radial-gradient(ellipse at 50% 85%,#8e0009,transparent 60%),linear-gradient(180deg,var(--red),#c10010 60%,#9d000a)}
.audience h2{position:absolute;top:122px;font-size:30px;font-weight:600}
.venues h2{left:172px;color:var(--white)}
.artists h2{left:25px;color:#333}
.points{position:absolute;list-style:none;font-size:11.5px;line-height:15px}
.points li{position:relative;padding-left:13px;margin-bottom:12px}
.points li::before{content:"";position:absolute;left:0;top:5px;width:6px;height:6px;border-radius:50%}
.venues .points{left:172px;top:184px;width:400px;color:var(--white)}
.venues .points li::before{background:var(--white)}
.artists .points{left:25px;top:184px;width:390px;color:#444}
.artists .points li{margin-bottom:10px}
.artists .points li::before{background:var(--red)}
.venue-note{position:absolute;left:172px;top:330px;width:420px;font-size:11.5px;line-height:23px;color:var(--white)}
.artist-cta{position:absolute;left:25px;top:389px;font-size:13px;font-weight:600;color:#222}
.inline-form{position:absolute;top:438px;height:41px;display:flex;border-radius:21px;overflow:hidden;font-size:12px}
.inline-form .field{flex:1;background:var(--white);padding:0 17px;display:flex;align-items:center;color:#555}
.inline-form .btn{width:104px;display:flex;align-items:center;justify-content:center;font-weight:600;color:var(--white)}
.venues .inline-form{left:172px;width:384px}
.venues .inline-form .btn{background:var(--black)}
.artists .inline-form{left:25px;width:386px}
.artists .inline-form .field{border:1px solid #ddd;border-right:0;border-radius:21px 0 0 21px}
.artists .inline-form .btn{background:var(--red)}

/* About */
.about-mark{position:absolute;left:572px;top:2746px;width:56px;height:56px;border-radius:50%;background:#111}
.about-text{position:absolute;left:260px;top:2886px;width:680px;text-align:center;font-size:12.5px;line-height:24px;color:#555}
.pill{position:absolute;background:var(--red);color:var(--white);font-weight:600;font-size:13px;border-radius:19px;display:flex;align-items:center;justify-content:center}

/* Contact */
.contact{position:absolute;left:0;top:3136px;width:1200px;height:582px}
.contact-photo{position:absolute;left:0;top:0;width:1200px;height:582px;clip-path:polygon(0 0,50% 62px,100% 0,100% 100%,0 100%);background:radial-gradient(ellipse at 70% 85%,#2a2a2a,transparent 60%),linear-gradient(180deg,#101010,#161616 70%,#0e0e0e)}
.contact .section-title{top:113px;color:var(--white)}
.footer-logo{position:absolute;left:172px;top:262px;font-size:44px;font-weight:500;color:var(--white)}
.socials{position:absolute;left:176px;top:404px;display:flex;gap:16px}
.socials span{width:26px;height:26px;border-radius:50%;border:2px solid var(--white)}
.info{position:absolute;left:383px;color:var(--white)}
.info h4{font-size:16px;font-weight:600;display:flex;align-items:center;gap:9px}
.info p{font-size:11.5px;line-height:22px;margin-top:6px}
.form-field{position:absolute;left:598px;width:393px;border-bottom:1px solid #cfcfcf;font-size:13px;color:var(--white)}
.site-footer{position:absolute;left:172px;top:514px;width:856px;border-top:1px solid #333;text-align:center;font-size:11.5px;color:#ddd;padding-top:26px}
</style>
</head>
<body>

<header class="site-header">
  <div class="logo"><span class="logo-dot"></span>TuneRoost</div>
  <div class="top-contact">
    <span><i class="round-ico"><svg width="12" height="12" viewBox="0 0 24 24"><path fill="#fff" d="M6.6 10.8a15 15 0 0 0 6.6 6.6l2.2-2.2c.3-.3.7-.4 1-.2 1.1.4 2.3.6 3.6.6.6 0 1 .4 1 1V20c0 .6-.4 1-1 1A17 17 0 0 1 3 4c0-.6.4-1 1-1h3.5c.6 0 1 .4 1 1 0 1.3.2 2.5.6 3.6.1.3 0 .7-.2 1z"/></svg></i>Phone: 124 555 0190</span>
    <span><i class="round-ico"><svg width="12" height="10" viewBox="0 0 24 18"><path fill="#fff" d="M0 0h24v18H0z"/><path fill="none" stroke="#d7000f" stroke-width="2" d="M1 1l11 9 11-9"/></svg></i>Email:info@tuneroost.com</span>
  </div>
  <nav class="main-nav"><span>Home</span><span>How TuneRoost Works</span><span>Why TuneRoost?</span><span>Venues</span><span>Artists</span><span>About TuneRoost</span><span>Contact</span></nav>
</header>

<section class="hero">
  <div class="hero-photo" role="img" aria-label="Photo of a rock band performing on a stage under red and green lights"></div>
  <h1>Zoomly for Live Music</h1>
  <p class="sub">TuneRoost connects venues with artists to make booking gigs simple</p>
  <div class="hero-form"><div class="field">Email Address:</div><div class="btn">Sign up now for FREE</div></div>
  <svg class="hero-edge" width="1200" height="80" viewBox="0 0 1200 80">
    <polygon fill="#d7000f" points="0,56 600,4 1200,56 1200,70 600,12 0,70"/>
    <polygon fill="#fff" points="0,70 600,12 1200,70 1200,80 0,80"/>
  </svg>
</section>

<h2 class="section-title" style="top:800px">How <b>TuneRoost</b> Works</h2>

<svg class="steps-svg" width="1200" height="300" viewBox="0 960 1200 300">
  <g stroke="#9a9a9a" stroke-width="1.5">
    <line x1="292" y1="1080" x2="365" y2="1114"/>
    <line x1="472" y1="1114" x2="545" y2="1080"/>
    <line x1="653" y1="1080" x2="726" y2="1114"/>
    <line x1="833" y1="1114" x2="906" y2="1080"/>
  </g>
  <g fill="none" stroke="#111" stroke-width="4">
    <path d="M238 1000 A58 58 0 1 0 296 1058"/>
    <path d="M419 1079 A58 58 0 1 1 361 1137"/>
    <path d="M599 1000 A58 58 0 1 0 657 1058"/>
    <path d="M780 1079 A58 58 0 1 1 722 1137"/>
    <path d="M960 1000 A58 58 0 1 0 1018 1058"/>
  </g>
  <g stroke="#111" stroke-width="2">
    <line x1="238" y1="1116" x2="238" y2="1172"/>
    <line x1="419" y1="1079" x2="419" y2="1027"/>
    <line x1="599" y1="1116" x2="599" y2="1172"/>
    <line x1="780" y1="1079" x2="780" y2="1027"/>
    <line x1="960" y1="1116" x2="960" y2="1172"/>
  </g>
  <g fill="#d7000f">
    <circle cx="238" cy="1172" r="6"/><circle cx="419" cy="1027" r="6"/><circle cx="599" cy="1172" r="6"/><circle cx="780" cy="1027" r="6"/><circle cx="960" cy="1172" r="6"/>
    <circle cx="232" cy="1046" r="9"/><path d="M214 1074c0-11 8-17 18-17s18 6 18 17z"/>
    <circle cx="253" cy="1070" r="7" stroke="#fff" stroke-width="2"/>
    <circle cx="426" cy="1130" r="14" fill="none" stroke="#d7000f" stroke-width="4"/>
    <line x1="416" y1="1140" x2="400" y2="1156" stroke="#d7000f" stroke-width="6" stroke-linecap="round"/>
    <circle cx="599" cy="1058" r="19"/><path d="M585 1070l-6 10 12-5z"/>
    <path fill="#fff" d="M592 1049c2-1 3 0 4 2l1 3-2 2c1 3 3 5 6 6l2-2 3 1c2 1 2 2 1 4-1 2-3 3-5 2-6-2-11-7-12-13 0-2 0-4 2-5z"/>
    <rect x="762" y="1122" width="36" height="32" rx="4"/>
    <rect x="768" y="1117" width="4" height="9" rx="2"/><rect x="788" y="1117" width="4" height="9" rx="2"/>
    <g fill="#fff"><rect x="767" y="1133" width="6" height="5"/><rect x="777" y="1133" width="6" height="5"/><rect x="787" y="1133" width="6" height="5"/><rect x="767" y="1142" width="6" height="5"/><rect x="777" y="1142" width="6" height="5"/><rect x="787" y="1142" width="6" height="5"/></g>
    <path d="M952 1040h16l-4 7c10 4 15 12 15 20 0 6-5 10-19 10s-19-4-19-10c0-8 5-16 15-20z"/>
    <text x="960" y="1071" font-size="18" font-weight="700" fill="#fff" text-anchor="middle" font-family="Jost,sans-serif">$</text>
  </g>
</svg>

<div class="step-num" style="left:178px;top:1180px">01</div>
<div class="step-text" style="left:168px;top:1228px">Artists and venues sign up for free and create a profile</div>
<div class="step-text" style="left:351px;top:906px">Venues search for an artist for their upcoming gigs</div>
<div class="step-num" style="left:359px;top:972px">02</div>
<div class="step-num" style="left:539px;top:1180px">03</div>
<div class="step-text" style="left:519px;top:1226px;width:170px">Venues request a quote and communicate with the artist direct</div>
<div class="step-text" style="left:690px;top:910px;width:180px">The gig is booked in once payment is provided by the venue.</div>
<div class="step-num" style="left:720px;top:972px">04</div>
<div class="step-num" style="left:900px;top:1180px">05</div>
<div class="step-text" style="left:891px;top:1227px">Upon completion the money is paid to the artist within 48 hours or less.</div>

<section class="why">
  <div class="why-photo" role="img" aria-label="Photo of a concert crowd with raised hands in the dark"></div>
  <h2 class="section-title">Why <b>TuneRoost?</b></h2>

  <div class="feature-card" style="left:172px">
    <svg width="100" height="100" viewBox="0 0 100 100"><circle cx="50" cy="50" r="45" fill="none" stroke="#fff" stroke-width="6"/><path d="M50 5A45 45 0 0 1 88 26" fill="none" stroke="#d7000f" stroke-width="6"/><path fill="#d7000f" d="M34 48h8v20h-8zM45 48l8-14c3 0 5 2 4 6l-2 6h11c3 0 4 3 3 5l-4 14c-1 2-2 3-4 3H45z"/></svg>
    <h3>Simple</h3><p>TuneRoost makes gig booking easy for both the venue and artist.</p>
  </div>
  <div class="feature-card" style="left:390px">
    <svg width="100" height="100" viewBox="0 0 100 100"><circle cx="50" cy="50" r="45" fill="none" stroke="#fff" stroke-width="6"/><path d="M50 5A45 45 0 0 1 88 26" fill="none" stroke="#d7000f" stroke-width="6"/><g fill="none" stroke="#d7000f" stroke-width="5" stroke-linecap="round"><path d="M30 44a28 28 0 0 1 40 0"/><path d="M37 52a18 18 0 0 1 26 0"/></g><circle cx="50" cy="62" r="5" fill="#d7000f"/></svg>
    <h3>Connect</h3><p>Join the TuneRoost community which is full of amazing artists and venues</p>
  </div>
  <div class="feature-card" style="left:606px">
    <svg width="100" height="100" viewBox="0 0 100 100"><circle cx="50" cy="50" r="45" fill="none" stroke="#fff" stroke-width="6"/><path d="M50 5A45 45 0 0 1 88 26" fill="none" stroke="#d7000f" stroke-width="6"/><path fill="#d7000f" d="M50 30l16 6v12c0 11-7 19-16 23-9-4-16-12-16-23V36z"/><path d="M43 50l5 5 10-10" fill="none" stroke="#fff" stroke-width="3"/></svg>
    <h3>Protection</h3><p>Everyone is protected with our complimentary dispute resolutions.</p>
  </div>
  <div class="feature-card" style="left:823px">
    <svg width="100" height="100" viewBox="0 0 100 100"><circle cx="50" cy="50" r="45" fill="none" stroke="#fff" stroke-width="6"/><path d="M50 5A45 45 0 0 1 88 26" fill="none" stroke="#d7000f" stroke-width="6"/><path fill="#d7000f" d="M30 50l20-20h16v16L46 66z"/><circle cx="59" cy="37" r="3" fill="#fff"/></svg>
    <h3>Price</h3><p>Get the best rate possible with TuneRoost only receiving 5% of the artists fee</p>
  </div>
</section>

<section class="audience venues">
  <div class="venue-photo" role="img" aria-label="Red-tinted photo of a festival crowd"></div>
  <h2>Venues</h2>
  <ul class="points">
    <li>TuneRoost is a 100% FREE service for all venues - you pay us nothing!</li>
    <li>Get instant access to hundreds of artists around your local community</li>
    <li>All genres to suit any venue from a pub to a wedding or even a nightclub</li>
    <li>Simple booking process with a money back guarantee</li>
    <li>Communicate directly with the artist and negotiate the price</li>
  </ul>
  <p class="venue-note">TuneRoost is not yet ready to host gigs as we're currently working on building our artists. We are launching for venues in Q4 2019. Pre-register now to keep informed and be one of the first people to use our platform.</p>
  <div class="inline-form"><div class="field">Email Address:</div><div class="btn">Pre Register</div></div>
</section>

<section class="audience artists">
  <h2>Artists</h2>
  <ul class="points">
    <li>Sign up to TuneRoost for FREE and get yourself in front of venues</li>
    <li>Only pay us if you get a gig - we only get 5% of the fee you charge the venue</li>
    <li>All genres and artists welcome - as long as you're experienced and professional</li>
    <li>Get paid within 48 hours or less after the gig guaranteed!</li>
    <li>Negotiate your price and don't pay huge agent fees to ensure you earn top dollar</li>
  </ul>
  <p class="artist-cta">Sign up and create your TuneRoost profile now</p>
  <div class="inline-form"><div class="field">Email Address:</div><div class="btn">Sign Up Now</div></div>
</section>

<span class="about-mark"></span>
<h2 class="section-title" style="top:2814px">About <b>TuneRoost</b></h2>
<p class="about-text">Sed ut perspiciatis unde omnis iste natus error sit voluptatem accusantium doloremque laudantium, totam rem aperiam, eaque ipsa quae ab illo inventore veritatis et quasi architecto beatae vitae dicta sunt explicabo. Nemo enim ipsam voluptatem quia voluptas sit aspernatur aut odit aut fugit, sed quia consequuntur magni dolores eos qui ratione voluptatem sequi nesciunt. Neque porro quisquam est, qui dolorem ipsum quia dolor sit amet, consectetur, adipisci velit, sed quia non numquam eius modi tempora incidunt ut labore et dolore magnam aliquam quaerat voluptatem. Ut enim ad minima veniam, quis nostrum exercitationem ullam corporis suscipit laboriosa</p>
<div class="pill" style="left:547px;top:3051px;width:106px;height:37px">Read More</div>

<section class="contact">
  <svg class="abs" style="left:0;top:0" width="1200" height="72" viewBox="0 0 1200 72">
    <polygon fill="#d7000f" points="0,0 600,52 1200,0 1200,12 600,64 0,12"/>
  </svg>
  <div class="contact-photo" role="img" aria-label="Dark photo of a concert audience"></div>
  <h2 class="section-title">Contact <b>TuneRoost</b></h2>

  <div class="footer-logo">TuneRoost</div>
  <div class="socials" aria-label="Social media links"><span></span><span></span><span></span><span></span></div>

  <div class="info" style="top:214px">
    <h4><svg width="16" height="20" viewBox="0 0 16 20"><path d="M8 1a7 7 0 0 1 7 7c0 5-7 11-7 11S1 13 1 8a7 7 0 0 1 7-7z" fill="none" stroke="#fff" stroke-width="1.4"/><circle cx="8" cy="8" r="2.5" fill="none" stroke="#fff" stroke-width="1.4"/></svg>Address</h4>
    <p>TuneRoost<br>Lorem ipsmdumodr 1211,<br>4821 TR,&nbsp; loremusilsik<br>Lindenveld</p>
  </div>
  <div class="info" style="top:356px">
    <h4><svg width="18" height="14" viewBox="0 0 18 14"><rect x="1" y="1" width="16" height="12" fill="none" stroke="#fff" stroke-width="1.4"/><path d="M1 1l8 7 8-7" fill="none" stroke="#fff" stroke-width="1.4"/></svg>Email</h4>
    <p>hello@tuneroost.com</p>
  </div>
  <div class="info" style="top:425px">
    <h4><svg width="18" height="18" viewBox="0 0 24 24"><path fill="none" stroke="#fff" stroke-width="1.6" d="M6.6 10.8a15 15 0 0 0 6.6 6.6l2.2-2.2c.3-.3.7-.4 1-.2 1.1.4 2.3.6 3.6.6.6 0 1 .4 1 1V20c0 .6-.4 1-1 1A17 17 0 0 1 3 4c0-.6.4-1 1-1h3.5c.6 0 1 .4 1 1 0 1.3.2 2.5.6 3.6.1.3 0 .7-.2 1z"/></svg>Phone</h4>
    <p>030-5550173</p>
  </div>

  <div class="form-field" style="top:206px;height:32px">Name:</div>
  <div class="form-field" style="top:252px;height:32px">Email:</div>
  <div class="form-field" style="top:297px;height:32px">Phone:</div>
  <div class="form-field" style="top:343px;height:74px">Message:</div>
  <div class="pill" style="left:598px;top:440px;width:95px;height:32px">Submit</div>

  <footer class="site-footer">© 2019 TuneRoost. All rights reserved.</footer>
</section>

</body>
</html>
```